We are a local Communty Pharmacy wishing to promote and market a specialised Pharmaceutical Service

We would like a design that is professional and enticing ( according to the brief In attached files)
We wish to Market Compounding Pharmacy as a specialist side of our business.
We have the expertise a purpose built preparation laboratory.
The main purpose is an Internet presence that entices prospective patients to contact or visit our physical store.

Target Market(s)

Patients Medicos and Veterinary clients

Industry/Entity Type

Pharmacy

Coding

Coded - Design and coding required

Number of Pages Required

1 page

Requirements
Must have
• Clear friendly image
Nice to have
• soft enticing feel
Should not have
• No crass loud unprofessional elements

```html
<!DOCTYPE html>
<html lang="en">
<head>
<meta charset="utf-8">
<title>Bramwell Compounding Pharmacy</title>
<link rel="stylesheet" href="https://fonts.googleapis.com/css2?family=Open+Sans:wght@400;600;700&display=swap">
<style>
:root{
  --navy:#1f3b70;
  --blue:#1e5fa8;
  --ink:#3a3a3a;
  --muted:#7a7a7a;
  --light:#ececec;
  --white:#ffffff;
  --footer:#2b2b2b;
  --footer-deep:#1c1c1c;
  --footer-text:#b9b9b9;
  --line:#444;
}
*{box-sizing:border-box;margin:0;padding:0}
html,body{width:745px;height:1200px;overflow:hidden}
body{font-family:"Open Sans",Arial,sans-serif;color:var(--ink);background:var(--white);font-size:9px}
.site-header{height:87px;display:flex;align-items:center;padding:0 55px;background:var(--white)}
.brand{display:flex;align-items:center;gap:8px;width:355px}
.brand-mark{width:22px;height:22px;background:var(--blue);border-radius:50%}
.brand-name{font-weight:700;font-size:17px;color:var(--navy);letter-spacing:.5px}
.header-info{display:flex;gap:8px;font-size:7px;line-height:1.45;color:var(--muted)}
.header-info .item{display:flex;gap:5px;align-items:flex-start}
.header-info .item:first-child{width:125px}
.header-info svg{flex:none;margin-top:1px}
.hero{position:relative;height:323px;background:linear-gradient(100deg,#c9cfd2 0%,#e3e5e3 35%,#b9a996 65%,#d8d4cc 100%)}
.hero-caption{position:absolute;left:0;right:0;top:150px;text-align:center;color:var(--white);padding:12px 0 14px;background:rgba(40,50,60,.45)}
.hero-caption h1{font-size:24px;font-weight:600;letter-spacing:1px}
.hero-caption .is{font-size:11px;margin:4px 0}
.hero-caption p{font-size:12px;letter-spacing:1px}
.hero-arrow{position:absolute;top:150px;width:22px;height:22px}
.hero-arrow.prev{left:14px}.hero-arrow.next{right:14px}
.intro{height:210px;text-align:center;padding:36px 62px 0}
.section-title{font-size:20px;font-weight:600;color:var(--ink);letter-spacing:.5px}
.rule{width:40px;height:2px;background:var(--blue);margin:6px auto 12px}
.intro p{font-size:7px;line-height:1.6;color:var(--muted);text-align:left}
.btn{display:inline-block;background:var(--navy);color:var(--white);font-size:7px;padding:6px 14px;border-radius:2px;margin-top:14px}
.features{height:298px;background:var(--light);text-align:center;padding-top:38px}
.cards{display:flex;justify-content:space-between;padding:0 62px;margin-top:4px}
.card{width:186px;background:var(--white);text-align:left;padding-bottom:10px}
.card-img{height:80px;display:block}
.card h3{font-size:9px;font-weight:600;margin:8px 10px 4px;color:var(--ink)}
.card p{font-size:7px;line-height:1.5;color:var(--muted);margin:0 10px}
.card .btn{margin:8px 10px 0;padding:4px 10px}
.site-footer{height:247px;background:var(--footer);color:var(--footer-text);display:flex;padding:32px 62px 0;gap:20px}
.col{flex:1}
.col h4{color:var(--white);font-size:12px;font-weight:600;margin-bottom:6px}
.col .rule{margin:0 0 14px;width:30px}
.col p{font-size:7px;line-height:1.9}
.row{display:flex;gap:6px;align-items:flex-start;font-size:7px;line-height:1.6;margin-bottom:8px}
.row svg{flex:none;margin-top:1px}
.map{width:180px;height:112px;background:linear-gradient(135deg,#dfe4ea,#c9d3dc)}
.bottom-bar{height:35px;background:var(--footer-deep);color:var(--footer-text);font-size:7px;display:flex;align-items:center;justify-content:space-between;padding:0 62px}
.social{display:flex;align-items:center;gap:6px}
.social span.dot{width:14px;height:14px;border-radius:50%;border:1px solid var(--footer-text)}
</style>
</head>
<body>
<header class="site-header">
  <div class="brand"><span class="brand-mark"></span><span class="brand-name">BRAMWELL</span></div>
  <div class="header-info">
    <div class="item">
      <svg width="8" height="10" viewBox="0 0 8 10"><path d="M4 0a3.5 3.5 0 0 0-3.5 3.5C.5 6 4 10 4 10s3.5-4 3.5-6.5A3.5 3.5 0 0 0 4 0z" fill="var(--blue)"/><circle cx="4" cy="3.5" r="1.2" fill="#fff"/></svg>
      <span>Bramwell Green Pharmacy<br>Unit 4 Linden Road, Bramwell<br>Western Australia</span>
    </div>
    <div class="item">
      <svg width="9" height="9" viewBox="0 0 10 10"><path d="M2 0l2 2.5-1.2 1.3a6 6 0 0 0 3.4 3.4L7.5 6 10 8l-1.5 2C4 10 0 6 0 1.5z" fill="var(--blue)"/></svg>
      <span>Phone : +(08) 9400 1234<br>Fax : +(08) 9400 1235<br>hello@bramwellpharmacy.example</span>
    </div>
  </div>
</header>

<section class="hero" role="img" aria-label="Photo of a smiling woman in glasses at a pharmacy counter with a pharmacist and shelves behind">
  <svg class="hero-arrow prev" viewBox="0 0 22 22"><circle cx="11" cy="11" r="10" fill="none" stroke="#fff" stroke-width="1.2"/><path d="M13 6l-5 5 5 5" fill="none" stroke="#fff" stroke-width="1.5"/></svg>
  <svg class="hero-arrow next" viewBox="0 0 22 22"><circle cx="11" cy="11" r="10" fill="none" stroke="#fff" stroke-width="1.2"/><path d="M9 6l5 5-5 5" fill="none" stroke="#fff" stroke-width="1.5"/></svg>
  <div class="hero-caption">
    <h1>COMPOUNDING PHARMACY</h1>
    <div class="is">is</div>
    <p>CUSTOMISED MEDICATIONS FOR PATIENTS</p>
  </div>
</section>

<section class="intro">
  <h2 class="section-title">WHAT IS COMPOUNDING PHARMACY?</h2>
  <div class="rule"></div>
  <p>Compounding is the craft of preparing medicines to the exact needs of each patient. Our pharmacists work in a purpose built laboratory to make creams, capsules, liquids and flavoured doses that are not available off the shelf. We help people with allergies, children who refuse bitter tastes, and pets that need the right strength for their size. Talk to our team today to learn how a personal formula could suit you and your family.</p>
  <span class="btn">View more info</span>
</section>

<section class="features">
  <h2 class="section-title">FEATURE ITEMS</h2>
  <div class="rule"></div>
  <div class="cards">
    <article class="card">
      <div class="card-img" role="img" aria-label="Photo of a pharmacist in a white coat at the counter" style="background:linear-gradient(135deg,#d9dde0,#a9b4bc)"></div>
      <h3>VET ARTICLE</h3>
      <p>Gentle doses made for pets, flavoured to suit each animal and its size.</p>
      <span class="btn">Read More</span>
    </article>
    <article class="card">
      <div class="card-img" role="img" aria-label="Photo of a hand applying cream to a shoulder" style="background:linear-gradient(135deg,#e8d6c8,#c9a98f)"></div>
      <h3>SCAR THERAPY</h3>
      <p>Soothing creams prepared to help skin heal and soften over time.</p>
      <span class="btn">Read More</span>
    </article>
    <article class="card">
      <div class="card-img" role="img" aria-label="Photo of a doctor examining a woman's neck" style="background:linear-gradient(135deg,#e6dfd8,#b8c2c8)"></div>
      <h3>THYROID EXTRACT</h3>
      <p>Carefully measured thyroid doses prepared to your doctor's exact script.</p>
      <span class="btn">Read More</span>
    </article>
  </div>
</section>

<footer class="site-footer">
  <div class="col">
    <h4>OPENING HOURS</h4><div class="rule"></div>
    <p>Mon to Sat 8:30 am - 6:00 pm<br>Sun 10:00 am - 5:00 pm</p>
  </div>
  <div class="col">
    <h4>LOCATION MAP</h4><div class="rule"></div>
    <div class="map" role="img" aria-label="Street map showing the pharmacy location"></div>
  </div>
  <div class="col">
    <h4>CONTACTS</h4><div class="rule"></div>
    <div class="row"><svg width="8" height="10" viewBox="0 0 8 10"><path d="M4 0a3.5 3.5 0 0 0-3.5 3.5C.5 6 4 10 4 10s3.5-4 3.5-6.5A3.5 3.5 0 0 0 4 0z" fill="var(--footer-text)"/></svg><span>Bramwell Green Pharmacy<br>Unit 4 Linden Road, Bramwell<br>Western Australia</span></div>
    <div class="row"><svg width="9" height="9" viewBox="0 0 10 10"><path d="M2 0l2 2.5-1.2 1.3a6 6 0 0 0 3.4 3.4L7.5 6 10 8l-1.5 2C4 10 0 6 0 1.5z" fill="var(--footer-text)"/></svg><span>+(08) 9400 1234</span></div>
    <div class="row"><svg width="9" height="9" viewBox="0 0 10 10"><rect x="0" y="1" width="10" height="8" fill="var(--footer-text)"/></svg><span>+(08) 9400 1235</span></div>
    <div class="row"><svg width="10" height="8" viewBox="0 0 10 8"><rect x=".5" y=".5" width="9" height="7" fill="none" stroke="var(--footer-text)"/><path d="M.5 .5l4.5 4 4.5-4" fill="none" stroke="var(--footer-text)"/></svg><span>hello@bramwellpharmacy.example</span></div>
  </div>
</footer>
<div class="bottom-bar">
  <span>© 2015 Compounding Pharmacy. All Rights Reserved.</span>
  <div class="social"><span>Connect with our social network</span><span class="dot"></span><span class="dot"></span><span class="dot"></span><span class="dot"></span></div>
</div>
</body>
</html>
```